Small butcher shop from Austria needs great powerpoint presentation

We are looking for a powerpoint template for our new CI - it should be modern and clear.

Logo (2 Versions), Slogan, Business Card and Car-Wrap-Design already exist. (See documents below.)

We won't use much text. About 50% of the presentation should be pictures, included in different ways.

We are a family business in Upper Austria, only process animals from farms in the immediate vicinity, produce the products by hand, value animal welfare and short transport routes and avoid packaging as much as possible.

The design should be modern and clear.

Sans Serif

• Use the red color sparingly. Only use sans serif fonts (Myriad Pro - if possible). The logo needs to be on first and last page only.

```html
<!DOCTYPE html>
<html lang="de">
<head>
<meta charset="utf-8">
<title>Holzner Fleischhauerei – Präsentation</title>
<link href="https://fonts.googleapis.com/css2?family=Oswald:wght@500;600&family=Source+Sans+3:wght@400;600&display=swap" rel="stylesheet">
<style>
  :root {
    --maroon: #7b1a2f;
    --maroon-dark: #5e1223;
    --ink: #2a2a2a;
    --muted: #555;
    --paper: #ffffff;
    --canvas: #e6e6e6;
    --wood: #2d2520;
    --meat: #9c3a3a;
    --grass: #6f8a3c;
    --sky: #a9c2d8;
    --head: "Oswald", sans-serif;
    --body: "Source Sans 3", sans-serif;
  }
  * { box-sizing: border-box; margin: 0; padding: 0; }
  html, body { width: 1200px; height: 4040px; overflow: hidden; }
  body { background: var(--canvas); font-family: var(--body); color: var(--ink); }
  .deck { padding: 14px 16px 0; }
  .slide {
    position: relative; width: 1168px; height: 657px; margin-bottom: 16px;
    background: var(--paper); overflow: hidden;
  }
  .photo { position: absolute; }
  .wordmark {
    position: absolute; display: flex; align-items: center; gap: 10px;
    font-family: var(--head); font-weight: 600; letter-spacing: 4px; color: var(--ink);
  }
  .wordmark .mark { width: 12px; height: 12px; background: currentColor; }
  .wordmark.light { color: #fff; }
  .wordmark.small { font-size: 30px; }
  .copy { font-size: 13px; line-height: 1.45; color: var(--muted); }
  .copy p + p { margin-top: 10px; }
  .headline {
    font-family: var(--head); font-weight: 500; text-transform: uppercase;
    color: var(--maroon); line-height: 1.05; letter-spacing: 1px;
  }

  /* Slide 1 – title */
  .title-bg { inset: 0; background: linear-gradient(180deg, #3a302a 0%, var(--wood) 55%, #5a2a26 80%, var(--meat) 100%); }
  .title .wordmark { left: 50%; top: 80px; transform: translateX(-50%); font-size: 78px; color: #fff; }

  /* Slide 2 – about */
  .about-photo { left: 0; top: 30px; width: 545px; height: 470px; background: linear-gradient(160deg, var(--sky) 0%, #8d8a86 45%, #3b4350 70%, var(--grass) 100%); }
  .about .wordmark { left: 40px; top: 560px; }
  .about-panel { position: absolute; left: 565px; top: 30px; width: 570px; height: 590px; background: var(--maroon); padding: 18px; }
  .about-panel .frame { border: 1px solid rgba(255,255,255,.55); height: 100%; padding: 40px 44px; }
  .about-panel h2 { font-family: var(--head); font-weight: 500; color: #fff; font-size: 38px; letter-spacing: 3px; text-align: right; margin-bottom: 36px; }
  .about-panel .copy { color: #f2e3e6; font-size: 15px; line-height: 1.55; }

  /* Slide 3 – intro grid */
  .intro .headline { position: absolute; left: 28px; top: 30px; width: 300px; font-size: 46px; }
  .intro .copy.left { position: absolute; left: 28px; top: 290px; width: 260px; }
  .intro .wordmark { left: 28px; top: 570px; }
  .ph-meat { left: 345px; top: 0; width: 365px; height: 262px; background: linear-gradient(135deg, #e5ddd6, #b3463f 60%, #7c2a2a); }
  .ph-herd { left: 310px; top: 280px; width: 400px; height: 290px; background: linear-gradient(180deg, var(--sky) 0%, #c9cfc9 40%, var(--grass) 75%, #4f6a2a); }
  .ph-sunset { left: 725px; top: 0; width: 443px; height: 232px; background: linear-gradient(180deg, #5d7db3 0%, #e7b56c 45%, var(--grass) 75%, #3f5a25); }
  .ph-butcher { left: 725px; top: 245px; width: 443px; height: 165px; background: linear-gradient(120deg, #3a3230, #a33a33 55%, #6b2a28); }
  .intro .copy.right { position: absolute; left: 728px; top: 425px; width: 420px; }

  /* Slide 4 – team */
  .team-band { position: absolute; left: 0; top: 0; width: 170px; height: 100%; background: var(--maroon); }
  .ph-portrait { left: 40px; top: 30px; width: 420px; height: 530px; background: linear-gradient(180deg, #4a3a32 0%, #8a6b5c 45%, #2e2e34 100%); }
  .team .wordmark { left: 22px; top: 596px; font-size: 22px; letter-spacing: 3px; }
  .team .headline { position: absolute; left: 580px; top: 40px; width: 560px; font-size: 46px; }
  .features { position: absolute; left: 580px; top: 200px; width: 560px; display: grid; grid-template-columns: 1fr 1fr; column-gap: 34px; row-gap: 26px; }
  .feature .tag { display: inline-block; background: var(--maroon); color: #fff; font-family: var(--head); font-size: 11px; letter-spacing: 1px; padding: 3px 10px; margin-bottom: 6px; }
  .feature h3 { font-family: var(--head); font-weight: 500; color: var(--maroon); font-size: 17px; text-transform: uppercase; margin-bottom: 6px; }

  /* Slide 5 – quality */
  .quality-panel { position: absolute; left: 0; top: 30px; width: 565px; height: 600px; background: var(--maroon); padding: 36px 40px; }
  .quality-panel .headline { color: #fff; font-size: 46px; margin-bottom: 30px; }
  .quality-panel .copy { color: #f2e3e6; font-size: 14px; }
  .quality .wordmark { left: 40px; top: 570px; }
  .photo-grid { position: absolute; left: 585px; top: 30px; width: 560px; height: 600px; display: grid; grid-template-columns: 1fr 1fr; gap: 12px; }
  .pg-cows { background: linear-gradient(180deg, var(--sky), #b7a48d 50%, var(--grass)); }
  .pg-cut { background: linear-gradient(135deg, #d9d0c8, #b23b3a 55%, #6e2424); }
  .pg-board { background: linear-gradient(135deg, #4a3b33, #a64a45 55%, #3a2c27); }
  .pg-cow { background: linear-gradient(180deg, #6f8fb8, #d9a25c 45%, #7a5230 75%, var(--grass)); }

  /* Slide 6 – closing */
  .ph-van { left: 0; top: 0; width: 1168px; height: 470px; background: linear-gradient(160deg, #bfcad6 0%, #8b8c8e 35%, #3a424f 62%, var(--grass) 85%, #4b6425); }
  .closing .accent { position: absolute; left: 0; top: 0; width: 14px; height: 470px; background: var(--maroon); }
  .closing .wordmark { left: 40px; top: 560px; font-size: 30px; }
  .closing .thanks { position: absolute; left: 360px; top: 510px; width: 420px; font-family: var(--head); font-weight: 500; font-size: 92px; color: var(--maroon); letter-spacing: 3px; line-height: 1; white-space: nowrap; }
  .contact { position: absolute; left: 830px; top: 512px; width: 320px; font-size: 16px; line-height: 1.55; color: var(--ink); font-style: normal; }
</style>
</head>
<body>
<main class="deck">

  <section class="slide title">
    <div class="photo title-bg" role="img" aria-label="Dark wooden table with raw cuts of beef and pork along the bottom edge"></div>
    <div class="wordmark"><span class="mark"></span>HOLZNER</div>
  </section>

  <section class="slide about">
    <div class="photo about-photo" role="img" aria-label="Branded delivery van parked in front of a rustic farm building"></div>
    <div class="wordmark small"><span class="mark"></span>HOLZNER</div>
    <div class="about-panel">
      <div class="frame">
        <h2>ABOUT US</h2>
        <div class="copy">
          <p>Lorem ipsum dolor sit amet, consectetur adipiscing elit, sed do eiusmod tempor incididunt ut labore et dolore magna aliqua. Quis ipsum suspendisse ultrices gravida. Risus commodo viverra maecenas accumsan lacus vel facilisis.</p>
          <p>Lorem ipsum dolor sit amet, consectetur adipiscing elit, sed do eiusmod tempor incididunt ut labore et dolore magna aliqua. Ut enim ad minim veniam, quis nostrud exercitation ullamco laboris nisi ut aliquip ex ea commodo consequat. Duis aute irure dolor in reprehenderit in voluptate velit esse cillum dolore eu fugiat nulla pariatur.</p>
          <p>Excepteur sint occaecat cupidatat non proident, sunt in culpa qui officia deserunt mollit anim id est laborum.</p>
        </div>
      </div>
    </div>
  </section>

  <section class="slide intro">
    <h2 class="headline">Lorem ipsum dol orsit consectetur adipiscing</h2>
    <div class="copy left"><p>Lorem ipsum dolor sit amet, consectetur adipiscing elit, sed do eiusmod tempor incididunt ut labore et dolore magna aliqua. Quis ipsum suspendisse ultrices gravida. Risus commodo viverra maecenas accumsan lacus vel facilisis. Duis aute irure dolor in reprehenderit in voluptate velit esse cillum dolore.</p></div>
    <div class="wordmark small"><span class="mark"></span>HOLZNER</div>
    <div class="photo ph-meat" role="img" aria-label="Hands preparing a piece of raw beef on a cutting board"></div>
    <div class="photo ph-herd" role="img" aria-label="Herd of black and white cows standing in a green pasture"></div>
    <div class="photo ph-sunset" role="img" aria-label="Cattle grazing on a meadow at sunset"></div>
    <div class="photo ph-butcher" role="img" aria-label="Butcher in a red shirt cutting meat at the counter"></div>
    <div class="copy right"><p>Lorem ipsum dolor sit amet, consectetur adipiscing elit, sed do eiusmod tempor incididunt ut labore et dolore magna aliqua. Quis ipsum suspendisse ultrices gravida. Risus commodo viverra maecenas accumsan lacus vel facilisis. Duis aute irure dolor in reprehenderit in voluptate velit esse cillum dolore eu fugiat nulla pariatur.</p></div>
  </section>

  <section class="slide team">
    <div class="team-band"></div>
    <div class="photo ph-portrait" role="img" aria-label="Portrait of a butcher in an apron standing in the shop"></div>
    <div class="wordmark light"><span class="mark"></span>HOLZNER</div>
    <h2 class="headline">Lorem ipsum dolorsitcon sectetur adipi.</h2>
    <div class="features">
      <article class="feature"><span class="tag">LOREM IPSUM</span><h3>Lorem ipsum dolor sit amet</h3><p class="copy">Lorem ipsum dolor sit amet, consectetur adipiscing elit, sed do eiusmod tempor incididunt ut labore et dolore magna aliqua.</p></article>
      <article class="feature"><span class="tag">LOREM IPSUM</span><h3>Lorem ipsum dolor sit amet</h3><p class="copy">Lorem ipsum dolor sit amet, consectetur adipiscing elit, sed do eiusmod tempor incididunt ut labore et dolore magna aliqua.</p></article>
      <article class="feature"><span class="tag">LOREM IPSUM</span><h3>Lorem ipsum dolor sit amet</h3><p class="copy">Lorem ipsum dolor sit amet, consectetur adipiscing elit, sed do eiusmod tempor incididunt ut labore et dolore magna aliqua.</p></article>
      <article class="feature"><span class="tag">LOREM IPSUM</span><h3>Lorem ipsum dolor sit amet</h3><p class="copy">Lorem ipsum dolor sit amet, consectetur adipiscing elit, sed do eiusmod tempor incididunt ut labore et dolore magna aliqua.</p></article>
    </div>
  </section>

  <section class="slide quality">
    <div class="quality-panel">
      <h2 class="headline">Lorem ipsum dolorsit consectetur adipi.</h2>
      <div class="copy">
        <p>Lorem ipsum dolor sit amet, consectetur adipiscing elit, sed do eiusmod tempor incididunt ut labore et dolore magna aliqua. Quis ipsum suspendisse ultrices gravida. Risus commodo viverra maecenas accumsan lacus vel facilisis.</p>
        <p>Lorem ipsum dolor sit amet, consectetur adipiscing elit, sed do eiusmod tempor incididunt ut labore et dolore magna aliqua. Ut enim ad minim veniam, quis nostrud exercitation ullamco laboris nisi ut aliquip ex ea commodo consequat. Duis aute irure dolor in reprehenderit in voluptate velit esse cillum dolore eu fugiat nulla pariatur.</p>
        <p>Excepteur sint occaecat cupidatat non proident, sunt in culpa qui officia deserunt mollit anim id est laborum.</p>
      </div>
    </div>
    <div class="wordmark small light"><span class="mark"></span>HOLZNER</div>
    <div class="photo-grid">
      <div class="pg-cows" role="img" aria-label="Brown cows grazing on a hillside meadow"></div>
      <div class="pg-cut" role="img" aria-label="Close-up of marbled raw steaks"></div>
      <div class="pg-board" role="img" aria-label="Assorted meat cuts on a wooden board"></div>
      <div class="pg-cow" role="img" aria-label="Single cow standing in a field at golden hour"></div>
    </div>
  </section>

  <section class="slide closing">
    <div class="photo ph-van" role="img" aria-label="Branded delivery van with meat cut names parked on a gravel yard"></div>
    <div class="accent"></div>
    <div class="wordmark"><span class="mark"></span>HOLZNER</div>
    <div class="thanks">THANK YOU</div>
    <address class="contact">
      Marktplatz 7 | 4880 Seewalchen<br>
      metzgerei@holzner-fleisch.at<br>
      www.holzner-fleisch.at<br>
      +43 660 123 45 67
    </address>
  </section>

</main>
</body>
</html>
```